Birchmoor Kell Executive Development Workshop Series

* Had error in first version of MS Word doc and have re-uploaded - twelve subject areas, not nine *
I'd like a flyer to print to hand out and post on my website birchmoorkell.com to advertise a workshop series I'm launching. I'd like it to build strongly on the wonderful logo you did and Scottish theme...and to have the same "feel" as my website. birchmoorkell.com
It should be 8.5x11, single sided. Not sure if I should use full color glossy or two-color on nice paper. Regardless, I will most likely have it done on a color copier and will not put it on a printing press.
I have typed up a document with all the information in a MS Word file, but need you to lay it out in an aesthetically pleasing way. I have attached that MS Word file.
I am also attaching a handful of similar flyer documents from other non-competing coaches in my network. I think they all have their merits, but leave me under-whelmed.
I'm also attaching a picture of me and some pictures of Scotland my parents took about 10 years ago. I'm reluctantly open to stock photos, just not too obvious or hackneyed (if that word can be applied to pictures as well as expressions).
Lastly, this workshop series will be an ongoing thing, so I'd like to be able to make minor edits myself with things like new dates or topics.
Thank you!
Target Market(s)
Small business owners and emerging leaders with large companies
Colors
Designer to choose colors to be used in the design.
Requirements
Should not have
- Obviously stock photos

```html
<!DOCTYPE html>
<html lang="en">
<head>
<meta charset="utf-8">
<title>Birchmoor Kell Executive Development Workshop Series</title>
<link href="https://fonts.googleapis.com/css2?family=Cinzel:wght@500&family=Lato:wght@400;700&display=swap" rel="stylesheet">
<style>
:root{
  --olive-dark:#434e2a;
  --olive-mid:#55612f;
  --sage:#c1d09b;
  --ink:#2b2f22;
  --paper:#ffffff;
  --footer:#262624;
  --stage:#ececec;
}
*{margin:0;padding:0;box-sizing:border-box}
html,body{width:1200px;height:1200px;overflow:hidden;background:var(--stage)}
body{font-family:'Lato',sans-serif;color:var(--ink)}
.flyer{position:absolute;left:148px;top:20px;width:1032px;height:1325px;background:var(--paper);transform:scale(.875);transform-origin:0 0;overflow:hidden}
.hero-photo{position:absolute;left:0;top:0;width:1032px;height:266px;background:linear-gradient(180deg,#d9dbd8 0%,#b8bdb4 35%,#6f7a5c 70%,#4d5a3a 100%)}
.hero-rule{position:absolute;left:0;width:1032px;background:var(--olive-dark)}
.logo-box{position:absolute;left:37px;top:36px;width:141px;height:139px;background:var(--olive-dark);display:flex;align-items:center;justify-content:center;text-align:center;color:#fff;font-size:17px;font-weight:700;line-height:1.2}
.portrait{position:absolute;left:831px;top:119px;width:157px;height:141px;background:linear-gradient(160deg,#5a5a62,#8c7d72 60%,#6c6a60);border:2px solid #fff}
.title-band{position:absolute;left:0;top:285px;width:1032px;height:153px;background:var(--sage)}
.tab{position:absolute;left:810px;top:261px;width:206px;height:51px;background:var(--olive-dark);color:#fff;font-weight:700;font-size:26px;display:flex;align-items:center;justify-content:center;box-shadow:0 6px 8px rgba(0,0,0,.25)}
.title-top{position:absolute;left:36px;top:306px;font-size:39px;color:var(--olive-dark);letter-spacing:-.5px}
.title-main{position:absolute;left:36px;top:356px;font-family:'Cinzel',serif;font-size:58px;color:var(--olive-dark);letter-spacing:1px;white-space:nowrap}
.intro{position:absolute;left:37px;top:459px;width:960px;font-size:14.3px;line-height:1.25}
.banner{position:absolute;left:0;top:532px;width:810px;height:53px;background:var(--olive-dark);clip-path:polygon(0 0,100% 0,98.5% 100%,0 100%);color:#fff;font-weight:700;font-size:14.3px;line-height:1.25;padding:6px 0 0 37px}
.topics{position:absolute;list-style:none;top:606px}
.topics.left{left:37px;width:480px}
.topics.right{left:526px;width:480px}
.topic{margin-bottom:18px}
.topic h3{font-size:18px;font-weight:700;color:var(--olive-dark);position:relative;padding-left:20px}
.topic h3::before{content:"";position:absolute;left:0;top:6px;width:9px;height:9px;border-radius:50%;background:var(--olive-dark)}
.topic p{font-size:14.3px;padding-left:33px;margin-top:6px;position:relative;line-height:1.25}
.topic p::before{content:"";position:absolute;left:21px;top:6px;width:4px;height:4px;background:var(--olive-dark)}
.includes{position:absolute;left:0;top:990px;width:532px;height:280px;background:var(--olive-mid);color:#fff}
.includes-tab{position:absolute;left:0;top:8px;width:406px;height:28px;background:var(--sage);color:var(--ink);clip-path:polygon(0 0,100% 0,98% 100%,0 100%);font-weight:700;font-size:14.3px;padding:5px 0 0 37px}
.includes ul{position:absolute;left:37px;top:58px;width:488px;list-style:none}
.includes li{font-size:14.3px;line-height:1.25;text-align:justify;padding-left:22px;position:relative;margin-bottom:8px}
.includes li::before{content:"";position:absolute;left:0;top:6px;width:8px;height:8px;border-radius:50%;background:var(--sage)}
.includes .note{position:absolute;left:35px;top:242px;font-size:14.3px;line-height:1.25}
.register{position:absolute;left:536px;top:970px;width:496px;height:258px;background:var(--sage);padding:20px 0 0 23px;font-size:14.3px;line-height:1.25}
.register .url{font-size:19px;font-weight:700}
.price{font-size:35px;margin-top:6px;line-height:1.1}
.commit{font-size:24px;margin-bottom:14px}
.contact{display:flex;justify-content:space-between;width:430px;margin-top:-6px;align-items:flex-end}
.contact .big{font-size:18px;display:flex;align-items:center;gap:5px}
.badge-strip{position:absolute;left:536px;top:1228px;width:496px;height:42px;background:var(--olive-mid)}
.badge{position:absolute;left:944px;top:1233px;width:47px;height:72px;background:#fff;border:2px solid #6b4f8a}
.footer{position:absolute;left:0;top:1270px;width:1032px;height:55px;background:var(--footer);color:#fff;font-size:19px;letter-spacing:3.5px;padding:12px 0 0 36px}
</style>
</head>
<body>
<main class="flyer">
  <div class="hero-photo" role="img" aria-label="Misty green highland valley between steep mountains"></div>
  <div class="hero-rule" style="top:266px;height:4px"></div>
  <div class="hero-rule" style="top:277px;height:3px"></div>
  <div class="logo-box">Birchmoor<br>Kell</div>
  <div class="portrait" role="img" aria-label="Portrait photo of the business coach"></div>
  <div class="title-band"></div>
  <div class="tab">First Thursdays</div>
  <h1 class="title-top">BIRCHMOOR KELL EXECUTIVE</h1>
  <h2 class="title-main">Development Workshop Series</h2>

  <p class="intro">A positive, fresh, results-driven approach for businesses to increase profits by building confidence, command and control in owners and executives. We will use proven leadership and business strategies to improve work-life balance, buy-in, and company value.&nbsp; Here’s your opportunity to meet with other like-minded business owners and executives once a month in a private and confidential setting</p>

  <div class="banner">We’ve got nine subject areas planned, and while they are all powerful, we will shift from high-level strategy topics to<br>“WHERE THE RUBBER MEETS THE ROAD” topics.</div>

  <ul class="topics left">
    <li class="topic"><h3>Sep 7 – My Company Owns Me :</h3><p>What a CEO should and should not do</p></li>
    <li class="topic"><h3>Oct 5 – Taking Vision / Mission / Values</h3><p>Down To The Molecular Level Of Your Company</p></li>
    <li class="topic"><h3>Nov 2 – People Problems</h3><p>The biggest waste of time and money for every small business</p></li>
    <li class="topic"><h3>Dec 7 – Value Delivery Systems</h3><p>Re-think everything you think you know about creating value</p></li>
    <li class="topic"><h3>Jan 4, 2018 – Rally Your Team Around A Goal</h3><p>How to create a meaningful company goal<br>and rally the troops around it</p></li>
    <li class="topic"><h3>Feb 1 – Building Your Executive Leadership Team</h3><p>You can’t succeed without one</p></li>
  </ul>
  <ul class="topics right">
    <li class="topic"><h3>Mar 1 – Improve Your Outside Sales Efforts</h3><p>Help your sales force to be busy AND successful</p></li>
    <li class="topic"><h3>Apr 5 – Every Brain In The Game</h3><p>Engage your team and build a strong culture</p></li>
    <li class="topic"><h3>May 3 – Repeatable Processes</h3><p>Coach your employees how to get predictable results every time</p></li>
    <li class="topic"><h3>Jun 7 – Finding and Filling Profit Holes</h3><p>Most small businesses waste more money than they profit</p></li>
    <li class="topic"><h3>*Jul 12 – Put Your Payroll On A Diet</h3><p>Why waste happens, what to do about it and how it helps everyone</p></li>
    <li class="topic"><h3>Aug 2 – Truly, How Effective Are You</h3><p>With This Whole “Leadership” Thing?</p></li>
  </ul>

  <section class="includes">
    <div class="includes-tab">Each month of this monthly workshop series includes:</div>
    <ul>
      <li>3-Hour Intensive Workshop: High-energy, creative sessions with engaging and relevant business topics, peer group advisory board (master mind), and networking (9am – 12pm, dates above)</li>
      <li><b>90-minute one-on-one coaching session:</b> to help you absorb and apply the revelations from the group sessions to your own business (mutually scheduled)</li>
      <li><b>Participation and trust is vital to your investment</b>; no holding back. Due to the confidential nature of the intensive workshops, all participants will sign a confidentiality agreement. Additionally, we will only allow one</li>
    </ul>
    <p class="note">All one-on-one coaching sessions will be mutually scheduled with Alan Drummond<br>once you have registered</p>
  </section>

  <section class="register">
    <p>To register, go to <span class="url">birchmoorkell.com/exec-dev</span> and click<br>the registration link</p>
    <p class="price">$395/month or $295/month</p>
    <p class="commit">with a 6-month or greater commitment</p>
    <p>All monthly Intensive Workshops will be 9am – 12pm on the dates<br>above at Loomhouse Coworking at 212 Mercer Lane,<br>Riverton NC 27000</p>
    <div class="contact">
      <div><p>Questions? Call Today!</p>
        <p class="big"><svg width="15" height="15" viewBox="0 0 16 16"><circle cx="8" cy="8" r="7.5" fill="none" stroke="#2b2f22"/><path d="M5 4l2 1-1 2 3 3 2-1 1 2-2 1c-3 0-6-3-6-6z" fill="#2b2f22"/></svg>555-014-2290</p></div>
      <div><p>Alan Drummond<br>Certified Professional Business Coach</p>
        <p class="big"><svg width="15" height="15" viewBox="0 0 16 16"><circle cx="8" cy="8" r="7.5" fill="none" stroke="#2b2f22"/><rect x="4" y="5" width="8" height="6" fill="none" stroke="#2b2f22"/><path d="M4 5l4 3 4-3" fill="none" stroke="#2b2f22"/></svg>alan@birchmoorkell.com</p></div>
    </div>
  </section>
  <div class="badge-strip"></div>
  <div class="footer">birchmoorkell.com</div>
  <div class="badge" aria-hidden="true"></div>
</main>
</body>
</html>
```